Expense Management Provider needs existinmg presentation reworked

We need to redesign the attached presentation to be better looking, aligned and homogenized

this is not a project from scratch ... but design ideas (incl for template are welcome )

I am very pressed in time . I have asked and paid for a 1 day delivery but that doesn't see to be reflected .... ???

Target Market(s)

finance management, travel management

Font styles to use
Sans Serif

Colors
3276b5
f37122
ec1f27

```html
<!DOCTYPE html>
<html lang="en">
<head>
<meta charset="utf-8">
<title>It Starts With a Calendar Entry</title>
<link rel="stylesheet" href="https://fonts.googleapis.com/css2?family=Titillium+Web:wght@400;600;700&display=swap">
<style>
  :root {
    --blue: #3276b5;
    --blue-dark: #1f5f9e;
    --navy: #0d6aa6;
    --orange: #f37122;
    --red: #ec1f27;
    --green: #27b03a;
    --text: #6b6b6b;
    --text-strong: #555555;
    --box-bg: #f7f7f7;
    --box-border: #d9d9d9;
    --icon-bg: #ececec;
    --arrow: #9a9a9a;
    --footer: #a8a8a8;
    --white: #ffffff;
  }
  * { box-sizing: border-box; margin: 0; padding: 0; }
  html, body { width: 1200px; height: 900px; overflow: hidden; background: var(--white); }
  body { font-family: "Titillium Web", Arial, sans-serif; position: relative; }

  .slide { position: relative; width: 1200px; height: 900px; background: var(--white); }

  .header-band {
    position: absolute; left: 0; top: 0; width: 1200px; height: 84px;
  }
  .slide-title {
    position: absolute; left: 27px; top: 12px;
    color: var(--white); font-size: 36px; font-weight: 700; letter-spacing: 0.5px;
    line-height: 48px;
  }
  .brand {
    position: absolute; right: 30px; top: 14px;
    display: flex; align-items: center; gap: 10px;
    color: var(--blue); font-size: 32px; font-weight: 700; line-height: 40px;
  }
  .brand-mark { width: 14px; height: 14px; background: var(--orange); }

  .flow { position: absolute; top: 207px; width: 405px; }
  .flow.left { left: 45px; }
  .flow.right { left: 750px; }

  .step {
    position: relative; height: 90px; width: 405px;
    background: linear-gradient(#fbfbfb, #efefef);
    border: 1px solid var(--box-border); border-radius: 8px;
    display: flex; align-items: center;
  }
  .step-label {
    flex: 1; padding-left: 18px;
    color: var(--text); font-size: 24px; line-height: 31px; font-weight: 400;
  }
  .step-label.centered { text-align: center; padding-left: 0; padding-right: 6px; }
  .step-label b { font-weight: 700; color: var(--text-strong); }
  .step-icon {
    width: 90px; height: 88px; background: var(--icon-bg);
    border-left: 1px solid var(--box-border); border-radius: 0 7px 7px 0;
    display: flex; align-items: center; justify-content: center;
  }
  .step-link { height: 46px; display: flex; justify-content: flex-start; padding-left: 85px; align-items: center; }

  .tag {
    position: absolute; top: 760px; height: 60px;
  }
  .tag.travel { left: 45px; width: 400px; }
  .tag.expense { left: 750px; width: 402px; }
  .tag-label {
    position: absolute; left: 0; top: 0; width: calc(100% - 24px); height: 60px;
    display: flex; align-items: center; justify-content: center;
    color: var(--white); font-size: 36px; font-weight: 700;
  }

  .flight-visual {
    position: absolute; left: 457px; top: 722px; width: 272px; height: 88px;
    background: linear-gradient(90deg, var(--navy), #2a7fb8);
    border-radius: 44px 10px 10px 44px; opacity: 0.9;
  }

  .footer {
    position: absolute; left: 0; bottom: 0; width: 1200px; height: 30px;
    background: var(--footer);
  }
  .copyright {
    position: absolute; left: 8px; top: 3px; color: var(--white); font-size: 15px; line-height: 24px;
  }
  .page-number {
    position: absolute; right: 20px; bottom: 0; width: 78px; height: 40px;
  }
  .page-number span {
    position: absolute; left: 0; top: 0; width: 78px; height: 40px;
    display: flex; align-items: center; justify-content: center;
    color: var(--white); font-size: 21px; font-weight: 600;
  }
</style>
</head>
<body>
<div class="slide">

  <svg class="header-band" viewBox="0 0 1200 84" aria-hidden="true">
    <defs>
      <linearGradient id="bandFill" x1="0" x2="1" y1="0" y2="0">
        <stop offset="0" stop-color="#3f86c6"/>
        <stop offset="1" stop-color="#2c6ead"/>
      </linearGradient>
    </defs>
    <polygon points="0,0 1200,0 1200,72 0,72" fill="url(#bandFill)"/>
    <polygon points="0,72 945,72 940,84 0,84" fill="var(--orange)"/>
    <polygon points="985,0 1200,0 1200,66 945,66" fill="var(--white)"/>
  </svg>
  <h1 class="slide-title">IT STARTS WITH A CALENDAR ENTRY</h1>
  <div class="brand"><span class="brand-mark"></span>TripLedger</div>

  <section class="flow left">
    <div class="step">
      <p class="step-label">Calendar Entry of<br><b>Remote Meeting</b></p>
      <div class="step-icon">
        <svg width="50" height="48" viewBox="0 0 50 48" aria-hidden="true">
          <rect x="3" y="7" width="44" height="38" rx="4" fill="none" stroke="var(--navy)" stroke-width="3"/>
          <rect x="3" y="7" width="44" height="9" fill="var(--navy)"/>
          <rect x="12" y="2" width="4" height="10" rx="2" fill="var(--navy)"/>
          <rect x="34" y="2" width="4" height="10" rx="2" fill="var(--navy)"/>
          <g fill="var(--navy)">
            <rect x="10" y="21" width="6" height="5"/><rect x="19" y="21" width="6" height="5"/><rect x="28" y="21" width="6" height="5"/><rect x="37" y="21" width="5" height="5"/>
            <rect x="10" y="29" width="6" height="5"/><rect x="19" y="29" width="6" height="5"/><rect x="28" y="29" width="6" height="5"/><rect x="37" y="29" width="5" height="5"/>
            <rect x="10" y="37" width="6" height="4"/><rect x="19" y="37" width="6" height="4"/><rect x="28" y="37" width="6" height="4"/>
          </g>
        </svg>
      </div>
    </div>
    <div class="step-link"><svg width="24" height="34" viewBox="0 0 24 34" aria-hidden="true"><path d="M12 2 V30 M2 20 L12 30 L22 20" fill="none" stroke="var(--arrow)" stroke-width="4"/></svg></div>
    <div class="step">
      <p class="step-label">New <b>Travel Request</b></p>
      <div class="step-icon">
        <svg width="70" height="34" viewBox="0 0 70 34" aria-hidden="true">
          <path d="M3 18 L13 28 L32 6" fill="none" stroke="var(--green)" stroke-width="6" stroke-linecap="round"/>
          <path d="M44 8 L64 28 M64 8 L44 28" stroke="var(--red)" stroke-width="6" stroke-linecap="round"/>
        </svg>
      </div>
    </div>
    <div class="step-link"><svg width="24" height="34" viewBox="0 0 24 34" aria-hidden="true"><path d="M12 2 V30 M2 20 L12 30 L22 20" fill="none" stroke="var(--arrow)" stroke-width="4"/></svg></div>
    <div class="step">
      <p class="step-label centered">Approval Email<br>With <b>Travel Options</b></p>
      <div class="step-icon">
        <svg width="56" height="56" viewBox="0 0 56 56" aria-hidden="true">
          <rect x="4" y="4" width="38" height="38" rx="9" fill="#2f7fe0"/>
          <rect x="11" y="15" width="24" height="17" rx="2" fill="var(--white)"/>
          <path d="M11 16 L23 26 L35 16" fill="none" stroke="#8fb8ea" stroke-width="2"/>
          <path d="M28 40 L36 48 L52 28" fill="none" stroke="var(--green)" stroke-width="6" stroke-linecap="round"/>
        </svg>
      </div>
    </div>
    <div class="step-link"><svg width="24" height="34" viewBox="0 0 24 34" aria-hidden="true"><path d="M12 2 V30 M2 20 L12 30 L22 20" fill="none" stroke="var(--arrow)" stroke-width="4"/></svg></div>
    <div class="step">
      <p class="step-label">Booking <b>Code Sent</b></p>
      <div class="step-icon">
        <svg width="62" height="44" viewBox="0 0 62 44" aria-hidden="true">
          <rect x="8" y="4" width="50" height="30" rx="3" fill="none" stroke="var(--navy)" stroke-width="3" transform="rotate(-6 33 19)"/>
          <rect x="4" y="10" width="50" height="30" rx="3" fill="var(--white)" stroke="var(--navy)" stroke-width="3"/>
          <line x1="40" y1="12" x2="40" y2="38" stroke="var(--navy)" stroke-width="2" stroke-dasharray="3 3"/>
          <path d="M12 25 L34 25 M22 18 L28 25 L22 32 M14 21 L16 25 L14 29" fill="none" stroke="var(--navy)" stroke-width="3"/>
        </svg>
      </div>
    </div>
  </section>

  <section class="flow right">
    <div class="step">
      <p class="step-label">Calendar Entry of<br><b>Remote Meeting</b></p>
      <div class="step-icon">
        <svg width="50" height="48" viewBox="0 0 50 48" aria-hidden="true">
          <rect x="3" y="7" width="44" height="38" rx="4" fill="none" stroke="var(--navy)" stroke-width="3"/>
          <rect x="3" y="7" width="44" height="9" fill="var(--navy)"/>
          <rect x="12" y="2" width="4" height="10" rx="2" fill="var(--navy)"/>
          <rect x="34" y="2" width="4" height="10" rx="2" fill="var(--navy)"/>
          <g fill="var(--navy)">
            <rect x="10" y="21" width="6" height="5"/><rect x="19" y="21" width="6" height="5"/><rect x="28" y="21" width="6" height="5"/><rect x="37" y="21" width="5" height="5"/>
            <rect x="10" y="29" width="6" height="5"/><rect x="19" y="29" width="6" height="5"/><rect x="28" y="29" width="6" height="5"/><rect x="37" y="29" width="5" height="5"/>
            <rect x="10" y="37" width="6" height="4"/><rect x="19" y="37" width="6" height="4"/><rect x="28" y="37" width="6" height="4"/>
          </g>
        </svg>
      </div>
    </div>
    <div class="step-link"><svg width="24" height="34" viewBox="0 0 24 34" aria-hidden="true"><path d="M12 2 V30 M2 20 L12 30 L22 20" fill="none" stroke="var(--arrow)" stroke-width="4"/></svg></div>
    <div class="step">
      <p class="step-label">New <b>Travel Request</b></p>
      <div class="step-icon">
        <svg width="70" height="34" viewBox="0 0 70 34" aria-hidden="true">
          <path d="M3 18 L13 28 L32 6" fill="none" stroke="var(--green)" stroke-width="6" stroke-linecap="round"/>
          <path d="M44 8 L64 28 M64 8 L44 28" stroke="var(--red)" stroke-width="6" stroke-linecap="round"/>
        </svg>
      </div>
    </div>
    <div class="step-link"><svg width="24" height="34" viewBox="0 0 24 34" aria-hidden="true"><path d="M12 2 V30 M2 20 L12 30 L22 20" fill="none" stroke="var(--arrow)" stroke-width="4"/></svg></div>
    <div class="step">
      <p class="step-label centered">Approval Email<br>With <b>Travel Options</b></p>
      <div class="step-icon">
        <svg width="56" height="56" viewBox="0 0 56 56" aria-hidden="true">
          <rect x="4" y="4" width="38" height="38" rx="9" fill="#2f7fe0"/>
          <rect x="11" y="15" width="24" height="17" rx="2" fill="var(--white)"/>
          <path d="M11 16 L23 26 L35 16" fill="none" stroke="#8fb8ea" stroke-width="2"/>
          <path d="M28 40 L36 48 L52 28" fill="none" stroke="var(--green)" stroke-width="6" stroke-linecap="round"/>
        </svg>
      </div>
    </div>
    <div class="step-link"><svg width="24" height="34" viewBox="0 0 24 34" aria-hidden="true"><path d="M12 2 V30 M2 20 L12 30 L22 20" fill="none" stroke="var(--arrow)" stroke-width="4"/></svg></div>
    <div class="step">
      <p class="step-label">Booking <b>Code Sent</b></p>
      <div class="step-icon">
        <svg width="62" height="44" viewBox="0 0 62 44" aria-hidden="true">
          <rect x="8" y="4" width="50" height="30" rx="3" fill="none" stroke="var(--navy)" stroke-width="3" transform="rotate(-6 33 19)"/>
          <rect x="4" y="10" width="50" height="30" rx="3" fill="var(--white)" stroke="var(--navy)" stroke-width="3"/>
          <line x1="40" y1="12" x2="40" y2="38" stroke="var(--navy)" stroke-width="2" stroke-dasharray="3 3"/>
          <path d="M12 25 L34 25 M22 18 L28 25 L22 32 M14 21 L16 25 L14 29" fill="none" stroke="var(--navy)" stroke-width="3"/>
        </svg>
      </div>
    </div>
  </section>

  <div class="tag travel">
    <svg width="400" height="60" viewBox="0 0 400 60" aria-hidden="true"><polygon points="0,0 376,0 400,30 376,60 0,60" fill="var(--orange)"/></svg>
    <span class="tag-label">Travel</span>
  </div>
  <div class="flight-visual" role="img" aria-label="Illustration of a blue airplane in flight"></div>
  <div class="tag expense">
    <svg width="402" height="60" viewBox="0 0 402 60" aria-hidden="true"><polygon points="0,0 378,0 402,30 378,60 0,60" fill="var(--orange)"/></svg>
    <span class="tag-label">Expense</span>
  </div>

  <footer class="footer">
    <p class="copyright">Copyright text here</p>
  </footer>
  <div class="page-number">
    <svg width="78" height="40" viewBox="0 0 78 40" aria-hidden="true"><polygon points="14,0 78,0 64,40 0,40" fill="var(--red)"/></svg>
    <span>01</span>
  </div>

</div>
</body>
</html>
```